Velan Tea Label & packaging for a premium tea brand. For local and global market

Create a look and feel for a box and rectangle tin. We are looking for a luxe packaging design for a new tea brand based in Kenya called 'Velan Tea'. Kenya is home to the finest teas in the world and Velan tea looks to embody that fact. Velan Tea uses the most premium of Kenyan Tea, Black tea, Purple tea, White Tea, Green tea, Hibiscus Tea and Moringa Tea. Velan Tea is handpicked from Kenya's highlands. This project will include the look and feel of the different teas described above. The copy on the main face of the box should read 'Premium Kenyan Tea' The box will contain 25 tagged tea bags, with a net weight of 50 gms.

On one side of the box will read 'packaging instructions' To fully savour this Velan premium tea, use one tea bag for each cup, add some freshly bolded water and wait for 2 minutes as you enjoy the sweet aroma of our tea, stir and serve' Ingredients : Black Tea, and for the others the same : Hibiscus Tea, Green Tea, Purple Tea, White tea. should also feature on the label: Produce of Kenya.

Target Market(s)

Premium

Industry/Entity Type

Agribusiness

Font styles to use
Script

Colors

Designer to choose colors to be used in the design.

Requirements
Must have
• Luxe look and feel
Nice to have
• I have attached the Velan tea logo and images of brands I'd lile the designer to be inspired by.
Should not have
• Green and yellow colours

```html
<!DOCTYPE html>
<html lang="en">
<head>
<meta charset="utf-8">
<title>Velan Tea – Tin Label</title>
<link rel="stylesheet" href="https://fonts.googleapis.com/css2?family=Gelasio:ital,wght@0,400;1,400&family=Bebas+Neue&display=swap">
<style>
  :root {
    --tin-black: #221f20;
    --ink-white: #ffffff;
    --rule-white: rgba(255,255,255,0.85);
    --flag-black: #111111;
    --flag-red: #bb1f25;
    --flag-green: #1c7a3a;
  }
  html, body {
    margin: 0;
    padding: 0;
    width: 1200px;
    height: 913px;
    overflow: hidden;
    background: var(--tin-black);
  }
  .label-face {
    position: relative;
    width: 1200px;
    height: 913px;
    background: var(--tin-black);
    color: var(--ink-white);
  }
  .brand-name {
    position: absolute;
    left: 0;
    width: 1200px;
    top: 200px;
    text-align: center;
    font-family: "Gelasio", Georgia, serif;
    font-weight: 400;
    font-size: 104px;
    line-height: 130px;
    letter-spacing: 4px;
    margin: 0;
  }
  .info-frame {
    position: absolute;
    left: 302px;
    top: 279px;
    width: 596px;
    height: 510px;
    border: 1px solid var(--rule-white);
    border-top: none;
    box-sizing: border-box;
  }
  .frame-top {
    position: absolute;
    top: 0;
    height: 1px;
    background: var(--rule-white);
  }
  .frame-top.left { left: 0; width: 129px; }
  .frame-top.right { right: 0; width: 128px; }
  .instructions {
    position: absolute;
    left: 40px;
    right: 40px;
    top: 58px;
    margin: 0;
    text-align: center;
    font-family: "Gelasio", Georgia, serif;
    font-style: italic;
    font-size: 34px;
    line-height: 42px;
    letter-spacing: 1.6px;
  }
  .origin {
    position: absolute;
    left: 0;
    right: 0;
    top: 433px;
    display: flex;
    justify-content: center;
    align-items: center;
    gap: 16px;
  }
  .origin-flag { width: 42px; height: 34px; display: block; }
  .origin-text {
    font-family: "Bebas Neue", Impact, sans-serif;
    font-size: 40px;
    line-height: 40px;
    letter-spacing: 1.5px;
    padding-top: 4px;
  }
</style>
</head>
<body>
  <main class="label-face">
    <h1 class="brand-name">VELAN</h1>
    <section class="info-frame">
      <span class="frame-top left"></span>
      <span class="frame-top right"></span>
      <p class="instructions">To fully savour this Velan<br>premium tea, use one tea<br>bag for each cup, add<br>some freshly bolded water<br>and wait for 2 minutes as<br>you enjoy the sweet aroma<br>of our tea, stir and serve'<br>Ingredients</p>
      <div class="origin">
        <svg class="origin-flag" viewBox="0 0 42 34" aria-hidden="true">
          <rect x="0" y="0" width="42" height="34" rx="3" fill="var(--ink-white)"/>
          <rect x="0" y="0" width="42" height="10" rx="3" fill="var(--flag-black)"/>
          <rect x="0" y="12" width="42" height="10" fill="var(--flag-red)"/>
          <rect x="0" y="24" width="42" height="10" rx="3" fill="var(--flag-green)"/>
        </svg>
        <span class="origin-text">Product of Kenya</span>
      </div>
    </section>
  </main>
</body>
</html>
```